KBT Business Cards

We require business cards for our business. We would like a matte black back to the card, with our logo centred in the middle. The front side of the card is open to design.

Target Market(s)

Clients looking for legal services (professional)

Industry/Entity Type

Legal

Contact Information for Business Card

Doran Kelbrath
Partner
Mobile: 0461 738 524
Email: doran@kbtlaw.co
Website: www.kbtlaw.co
Level 3, 118 Wendmore Street
Sydney NSW 2000

Font styles to use
Other font styles liked:
• Avenir

Colors
f04a50
ffffff
1b1b1b

Requirements
Must have
• Black back with logo included in the centre of the card.
• Our font is Avenir.

```html
<!DOCTYPE html>
<html lang="en">
<head>
<meta charset="utf-8">
<title>KBT Legal Business Cards</title>
<link rel="stylesheet" href="https://fonts.googleapis.com/css2?family=Nunito+Sans:wght@400;600;700&display=swap">
<style>
  :root {
    --brand-red: #f04a50;
    --brand-crimson: #d81d4f;
    --ink: #1b1b1b;
    --card-black: #060708;
    --paper: #ffffff;
    --backdrop: #9a9a9a;
  }
  * { box-sizing: border-box; margin: 0; padding: 0; }
  html, body {
    width: 1200px; height: 930px; overflow: hidden;
    background: var(--backdrop);
    font-family: "Nunito Sans", "Avenir", sans-serif;
  }
  .canvas { position: relative; width: 1200px; height: 930px; }

  .card {
    position: absolute; width: 540px; height: 309px; overflow: hidden;
  }
  .card--back { left: 90px; top: 100px; background: var(--card-black); }
  .card--front { left: 570px; top: 520px; background: var(--paper); }

  .wordmark {
    position: absolute; display: flex; align-items: center; gap: 14px;
    font-weight: 700; font-size: 40px; letter-spacing: 2px; line-height: 1;
    white-space: nowrap;
  }
  .wordmark__square { width: 30px; height: 30px; background: var(--brand-crimson); flex: none; }
  .card--back .wordmark { left: 50%; top: 50%; transform: translate(-50%, -50%); color: var(--paper); }
  .card--front .wordmark { left: 32px; top: 174px; color: var(--ink); font-size: 26px; letter-spacing: 1.5px; gap: 10px; }
  .card--front .wordmark__square { width: 22px; height: 22px; }

  .divider {
    position: absolute; left: 262px; top: 70px; width: 1.5px; height: 160px;
    background: var(--brand-crimson);
  }

  .contact { position: absolute; left: 284px; top: 66px; color: var(--ink); }
  .contact__name {
    color: var(--brand-crimson); font-weight: 600; font-size: 21px;
    text-transform: uppercase; letter-spacing: 0.3px; line-height: 1.1;
    white-space: nowrap;
  }
  .contact__role { font-size: 13px; margin-top: 2px; }
  .contact__address { font-size: 13px; line-height: 1.35; margin-top: 10px; white-space: nowrap; }
  .contact__list { list-style: none; margin-top: 8px; font-size: 13px; line-height: 1.45; }
  .contact__list li { display: flex; align-items: center; gap: 8px; white-space: nowrap; }
  .contact__list svg { width: 10px; height: 10px; flex: none; }

  .edge-band { position: absolute; left: 0; bottom: 0; width: 540px; height: 22px; }
</style>
</head>
<body>
<main class="canvas">
  <section class="card card--back" aria-label="Card back">
    <div class="wordmark"><span class="wordmark__square"></span>KBT LEGAL</div>
  </section>

  <section class="card card--front" aria-label="Card front">
    <div class="wordmark"><span class="wordmark__square"></span>KBT LEGAL</div>
    <div class="divider"></div>
    <div class="contact">
      <p class="contact__name">Doran Kelbrath</p>
      <p class="contact__role">Partner</p>
      <p class="contact__address">Level 3, 118 Wendmore Street<br>Sydney NSW 2000</p>
      <ul class="contact__list">
        <li>
          <svg viewBox="0 0 10 10" aria-hidden="true"><path d="M2 1 L4 3 L3 4 Q4 6 6 7 L7 6 L9 8 L8 9.5 Q2 8.5 0.5 2 Z" fill="var(--brand-crimson)"/></svg>
          0461 738 524
        </li>
        <li>
          <svg viewBox="0 0 10 10" aria-hidden="true"><rect x="0.7" y="2" width="8.6" height="6" fill="none" stroke="var(--brand-crimson)" stroke-width="1"/><path d="M0.7 2 L5 5.5 L9.3 2" fill="none" stroke="var(--brand-crimson)" stroke-width="1"/></svg>
          doran@kbtlaw.co
        </li>
        <li>
          <svg viewBox="0 0 10 10" aria-hidden="true"><circle cx="5" cy="5" r="4.3" fill="none" stroke="var(--brand-crimson)" stroke-width="1"/><ellipse cx="5" cy="5" rx="1.8" ry="4.3" fill="none" stroke="var(--brand-crimson)" stroke-width="0.8"/><line x1="0.7" y1="5" x2="9.3" y2="5" stroke="var(--brand-crimson)" stroke-width="0.8"/></svg>
          www.kbtlaw.co
        </li>
      </ul>
    </div>
    <svg class="edge-band" viewBox="0 0 540 22" aria-hidden="true">
      <polygon points="0,14 372,14 372,22 0,22" fill="var(--brand-red)"/>
      <polygon points="372,0 540,0 540,22 352,22 352,14 368,14" fill="var(--ink)"/>
      <polygon points="352,14 372,14 372,22 352,22" fill="var(--brand-red)"/>
    </svg>
  </section>
</main>
</body>
</html>
```